Logo, Web and Mobile Designs for enterprise social media platform

All the details are in the attached document, please start reading the scope document first which explains what is this project about and the details about the needed deliverables, after that please read the UI_Requirements document which will detail what is expected regarding the coded web version since this is a coded contest, it is very important that you meet the UI requirements or suggest something else but we will need to agree first before working on the coded version

Good Luck

Target Market(s)

Enterprise Social Media

Industry/Entity Type

Media

Coding

Coded - Design and coding required

Number of Pages Required

5+ page

Font styles to use
Sans Serif

Requirements
Must have
• All the must haves are listed in the scope document so please check before you start

```html
<!DOCTYPE html>
<html lang="en">
<head>
<meta charset="utf-8">
<title>Teamora – Security Details</title>
<link href="https://fonts.googleapis.com/css2?family=Roboto:wght@300;400;500&display=swap" rel="stylesheet">
<style>
:root{
  --brand:#1e8ec8;
  --footer:#1e8bb8;
  --bg:#ebebeb;
  --side:#f4f4f4;
  --line:#e2e2e2;
  --text:#555;
  --muted:#777;
  --orange:#f59a1b;
  --white:#fff;
}
*{box-sizing:border-box;margin:0;padding:0}
html,body{width:1200px;height:826px;overflow:hidden}
body{font-family:'Roboto',sans-serif;background:var(--bg);color:var(--text);position:relative}
.abs{position:absolute}
/* header */
.topbar{left:0;top:0;width:1200px;height:70px;background:var(--white);border-bottom:1px solid #dcdcdc}
.vline{top:0;width:1px;height:70px;background:#e6e6e6}
.menu-btn{left:101px;top:29px}
.brand{left:167px;top:14px;display:flex;align-items:center;gap:8px;font-size:31px;font-weight:500;color:var(--brand)}
.brand-dot{width:40px;height:40px;border-radius:50%;background:var(--orange)}
.user{left:746px;top:19px;display:flex;align-items:center;gap:12px;font-size:17px;color:#555}
.avatar{width:34px;height:34px;border-radius:50%;background:linear-gradient(#8a7a6c,#3c3430)}
.badge{width:20px;height:16px;border-radius:8px;font-size:11px;color:#fff;text-align:center;line-height:16px}
/* card */
.card{left:99px;top:105px;width:1001px;height:533px;background:var(--white);border:1px solid #ddd}
.sidebar{left:0;top:0;width:279px;height:531px;background:var(--side);border-right:1px solid #ddd}
.side-main{position:absolute;left:17px;display:flex;align-items:center;gap:14px;font-size:16px;color:#444}
.side-sep{position:absolute;left:0;width:279px;height:1px;background:#e4e4e4}
.side-item{position:absolute;left:18px;font-size:16px;color:#555;display:flex;gap:16px;align-items:center}
.side-item.active{color:var(--brand);font-weight:500}
.panel{left:310px;top:40px;width:661px;height:454px;border:1px solid #e6e6e6;background:#fff}
.panel-head{height:49px;background:#f5f6f8;border-bottom:1px solid #e3e3e3;display:flex;align-items:center;gap:10px;padding-left:22px;font-size:16px;color:#444}
.label{position:absolute;left:22px;font-size:15px;color:#555}
.field{position:absolute;left:186px;border:1px solid #e0e0e0;background:#fff;font-size:11px;color:#444;display:flex;align-items:center}
.chip-ava{width:22px;height:22px;margin:0 7px 0 10px;background:linear-gradient(#c9b9a8,#7d6a5c)}
.plus{position:absolute;right:5px;top:8px;width:22px;height:22px;background:var(--brand);color:#fff;text-align:center;line-height:21px;font-size:14px}
.btn{position:absolute;left:185px;background:var(--brand);color:#fff;font-weight:500;text-align:center;border-radius:2px;box-shadow:0 2px 0 #156c99}
/* footer */
.footer{left:0;top:678px;width:1200px;height:148px;background:var(--footer);color:#fff;text-align:center}
.socials{position:absolute;left:513px;top:29px;display:flex;gap:13px}
.socials span{width:24px;height:24px;background:#fff;border-radius:4px}
.links{position:absolute;left:0;width:1200px;top:70px;font-size:14px;font-weight:300}
.copy{position:absolute;left:0;width:1200px;top:102px;font-size:14px}
</style>
</head>
<body>
<header class="topbar abs">
  <svg class="abs menu-btn" width="18" height="16"><rect y="0" width="18" height="3" fill="#888"/><rect y="6" width="18" height="3" fill="#888"/><rect y="12" width="18" height="3" fill="#888"/></svg>
  <div class="vline abs" style="left:144px"></div>
  <div class="brand abs"><span class="brand-dot"></span>Teamora</div>
  <div class="user abs"><span class="avatar" role="img" aria-label="User profile photo"></span>Alex Rivera
    <svg width="12" height="8"><path d="M0 0h12L6 7z" fill="#555"/></svg></div>
  <div class="vline abs" style="left:922px"></div>
  <div class="vline abs" style="left:991px"></div>
  <div class="vline abs" style="left:1051px"></div>
  <svg class="abs" style="left:946px;top:27px" width="20" height="18"><rect width="20" height="4" fill="#777"/><rect y="7" width="20" height="4" fill="#777"/><rect y="14" width="20" height="4" fill="#777"/></svg>
  <div class="badge abs" style="left:957px;top:16px;background:var(--orange)">8</div>
  <svg class="abs" style="left:1011px;top:26px" width="20" height="20"><circle cx="8" cy="8" r="6" fill="none" stroke="#777" stroke-width="3"/><path d="M12 12l6 6" stroke="#777" stroke-width="3"/></svg>
  <svg class="abs" style="left:1072px;top:26px" width="20" height="20"><path d="M10 1c-4 0-6 3-6 7v5l-3 3h18l-3-3V8c0-4-2-7-6-7z" fill="#777"/><circle cx="10" cy="18" r="2" fill="#777"/></svg>
  <div class="badge abs" style="left:1079px;top:16px;background:var(--brand)">8</div>
</header>

<main class="card abs">
  <nav class="sidebar abs">
    <div class="side-main" style="top:24px">
      <svg width="15" height="15"><rect width="6" height="6" fill="#1e8ec8"/><rect x="8" width="7" height="6" fill="#1e8ec8"/><rect y="8" width="6" height="7" fill="#1e8ec8"/><rect x="8" y="8" width="7" height="7" fill="#1e8ec8"/></svg>VIEW DASHBOARD</div>
    <div class="side-sep" style="top:59px"></div>
    <div class="side-main" style="top:79px">
      <svg width="15" height="15"><rect y="2" width="15" height="13" fill="none" stroke="#1e8ec8" stroke-width="2"/><rect y="2" width="15" height="4" fill="#1e8ec8"/></svg>VIEW EVENT</div>
    <div class="side-sep" style="top:115px"></div>
    <div class="side-item" style="top:147px">›<span>About Us</span></div>
    <div class="side-item" style="top:180px">›<span>Speakers</span></div>
    <div class="side-item" style="top:212px">›<span>Track</span></div>
    <div class="side-item" style="top:245px">›<span>Sessions</span></div>
    <div class="side-item" style="top:277px">›<span>Tickets</span></div>
    <div class="side-item" style="top:310px">›<span>Organizers</span></div>
    <div class="side-item" style="top:343px">›<span>Sponsors</span></div>
    <div class="side-item" style="top:375px">›<span>Exhibitor</span></div>
    <div class="side-item active" style="top:408px">›<span>SECURITY</span></div>
    <div class="side-item" style="top:440px">›<span>Members</span></div>
  </nav>

  <section class="panel abs">
    <div class="panel-head">
      <svg width="12" height="14"><path d="M3 6V4a3 3 0 0 1 6 0" fill="none" stroke="#555" stroke-width="2"/><rect y="6" width="12" height="8" fill="#555"/></svg>SECURITY DETAILS</div>
    <div class="label" style="top:94px">Event Type :</div>
    <div class="abs" style="left:185px;top:97px;font-size:12px;color:#666">PRIVATE</div>
    <div class="abs" style="left:237px;top:92px;width:48px;height:24px;border-radius:12px;border:1px solid #ddd;background:#f6f6f6"><span class="abs" style="left:3px;top:3px;width:16px;height:16px;border-radius:50%;background:#555"></span></div>
    <div class="btn" style="top:132px;width:94px;height:31px;line-height:31px;font-size:16px">SAVE</div>

    <div class="label" style="top:194px">Members :</div>
    <div class="field" style="top:184px;width:451px;height:38px;padding-left:18px">User Search</div>
    <div class="field" style="top:232px;width:301px;height:38px"><span class="chip-ava" role="img" aria-label="Member photo"></span>lmorgan.reed<span class="plus">+</span></div>

    <div class="label" style="top:297px">Administrators :</div>
    <div class="field" style="top:287px;width:451px;height:38px;padding-left:18px">User Search</div>
    <div class="field" style="top:335px;width:301px;height:38px"><span class="chip-ava" role="img" aria-label="Administrator photo"></span>lmorgan.reed<span class="plus">+</span></div>

    <div class="btn" style="top:391px;width:182px;height:35px;line-height:35px;font-size:16px">SEND INVITATION</div>
  </section>
</main>

<footer class="footer abs">
  <div class="socials"><span></span><span></span><span></span><span></span><span></span></div>
  <div class="links">Home &nbsp; / &nbsp;Contact &nbsp; / &nbsp;Topics &nbsp; / &nbsp;Posts and Comments &nbsp; / &nbsp;Discussion &nbsp; / &nbsp;Videos Links</div>
  <div class="copy">Copyright @ 2015 - 2015.Teamora. All Rights Reserved.</div>
</footer>
</body>
</html>
```